Heron Property Inspection business card

I am the principal inspector of Heron Property Inspections. I serve Northern Virginia from Winchester to Arlington.Associate, Federated Guild of Dwelling Examiners (FGDE)Graduate, FGDE Home Inspectors CourseNational Association of Home Inspectors ExamI'd like the business card to look more professional than comical.I pulled the attached picture off the web. I'd like to have something like that or an image of a house as my logo on the cards.

Target Market(s)

Persons who recently purchased a home.

Industry/Entity Type

Business

Contact Information for Business Card

Bob AllenBadger Home Inspections, LLC.4455 River RoadBluemont, Virginia 20135cell: 703-231-6680e-mail: tkmarlow@postvale.net

Font styles to use
Serif
Sans Serif

Requirements
Must have
• I'd like to have a logo, something that identifies me as a home inspector. The attached images are something that I'd like to have incorporated into my business card logo.
Nice to have
• I'd like a sketch of a house and/or a magnifying glass showing a house being inspected. The attached images are used as a suggestion only, I do not own the images.
Should not have
• Gimmicky stuff. I want to appear professional and trustworthy.

```html
<!DOCTYPE html>
<html lang="en">
<head>
<meta charset="utf-8">
<title>Heron Property Inspections – Business Card</title>
<link rel="stylesheet" href="https://fonts.googleapis.com/css2?family=Arimo:wght@400;700&display=swap">
<style>
  :root {
    --backdrop: #4a3b2e;
    --card-top: #1a1a1a;
    --card-bottom: #030303;
    --brand-blue: #3a6fc4;
    --name-cyan: #4cc3e0;
    --text-white: #f2f2f2;
    --icon-blue: #3d6bb5;
  }
  * { box-sizing: border-box; margin: 0; padding: 0; }
  html, body {
    width: 1200px; height: 892px; overflow: hidden;
    background: var(--backdrop);
    font-family: "Arimo", Arial, sans-serif;
  }
  .canvas {
    width: 1200px; height: 892px;
    display: flex; flex-direction: column;
    align-items: center; justify-content: center; gap: 40px;
  }
  .card {
    position: relative;
    width: 660px; height: 377px;
    border-radius: 22px;
    background: linear-gradient(160deg, var(--card-top) 0%, var(--card-bottom) 60%);
    box-shadow: 0 14px 30px rgba(0,0,0,.45);
    overflow: hidden;
  }
  /* Front */
  .card-front { display: flex; align-items: center; justify-content: center; }
  .brand { display: flex; align-items: center; gap: 22px; }
  .brand-dot {
    width: 64px; height: 64px; border-radius: 50%;
    background: var(--brand-blue);
    flex: none;
  }
  .brand-name {
    color: var(--brand-blue);
    font-weight: 700;
    font-size: 34px;
    line-height: 1.18;
    letter-spacing: -0.3px;
  }
  /* Back */
  .card-back { padding: 58px 62px 0 0; }
  .contact {
    position: absolute; right: 62px; top: 60px;
    text-align: right; color: var(--text-white);
  }
  .contact-name {
    color: var(--name-cyan);
    font-size: 40px; line-height: 1.1; letter-spacing: -0.5px;
  }
  .contact-role { font-size: 22px; margin-top: 4px; }
  .contact-lines { margin-top: 30px; font-size: 21px; line-height: 1.32; }
  .contact-icons {
    position: absolute; right: -2px; top: 0;
  }
  .icon-row { display: flex; gap: 8px; justify-content: flex-end; margin-top: 10px; }
  .icon-box {
    width: 34px; height: 34px; border-radius: 3px;
    background: var(--icon-blue);
    border: 1px solid #8fb0e6;
    display: flex; align-items: center; justify-content: center;
  }
</style>
</head>
<body>
  <main class="canvas">
    <section class="card card-front" aria-label="Card front">
      <div class="brand">
        <span class="brand-dot" aria-hidden="true"></span>
        <div class="brand-name">Heron Property<br>Inspections, LLC</div>
      </div>
    </section>

    <section class="card card-back" aria-label="Card back">
      <div class="contact">
        <div class="contact-name">Employee Name</div>
        <div class="contact-role">Your Position</div>
        <div class="icon-row">
          <span class="icon-box" aria-label="Phone">
            <svg width="18" height="22" viewBox="0 0 18 22" aria-hidden="true">
              <rect x="2" y="1" width="14" height="20" rx="2" fill="none" stroke="#fff" stroke-width="2"/>
              <rect x="5" y="4" width="8" height="7" fill="#fff"/>
              <circle cx="9" cy="16.5" r="1.6" fill="#fff"/>
            </svg>
          </span>
          <span class="icon-box" aria-label="Email">
            <svg width="22" height="16" viewBox="0 0 22 16" aria-hidden="true">
              <rect x="1" y="1" width="20" height="14" fill="none" stroke="#fff" stroke-width="2"/>
              <path d="M1 1 L11 9 L21 1 M1 15 L8 7 M21 15 L14 7" fill="none" stroke="#fff" stroke-width="1.8"/>
            </svg>
          </span>
        </div>
        <div class="contact-lines">
          <div class="contact-phone">703-555-0192</div>
          <div class="contact-email">tkmarlow@postvale.net</div>
          <div class="contact-street">7182 Quarry Lane Fernhill,</div>
          <div class="contact-city">Virginia 20148</div>
        </div>
      </div>
    </section>
  </main>
</body>
</html>
```